VENTURE CAPITAL GROUP BUSINESS CARD DESIGN

Venture Capital Group based in SF looking for a bold business card design. No trendy colour explosion, 3D effects etc. Just "simple" optical effects. Works on your brain, keeps your eye focused and sticks to your mind.
Target Market(s)
Technology startups
Industry/Entity Type
Venture Capital
Contact Information for Business Card
DESMOND WHITLAKE
MANAGING PARTNER
187 FENWORTH ST SAN FRANCISCO, CA 94187
415.555.0142 O
415.555.0147 F
415.555.0193 C
desmond@veldtmoorcapital.ventures

```html
<!DOCTYPE html>
<html lang="en">
<head>
<meta charset="utf-8">
<title>Veldtmoor Capital Group – Business Card</title>
<link rel="stylesheet" href="https://fonts.googleapis.com/css2?family=Marcellus&family=Saira+Semi+Condensed:wght@600&family=Lora&display=swap">
<style>
  :root {
    --backdrop: #a9a7a8;
    --green-light: #5bb94f;
    --green-mid: #2e8f45;
    --green-dark: #17683a;
    --green-brand: #1f7f3c;
    --paper: #fbfbfa;
    --silver: #9a9a9a;
    --silver-light: #d6d6d6;
    --ink: #5a5a5a;
    --white: #ffffff;
  }
  * { box-sizing: border-box; margin: 0; padding: 0; }
  html, body { width: 1200px; height: 1200px; overflow: hidden; }
  body { background: var(--backdrop); position: relative; font-family: "Lora", serif; }

  .card { position: absolute; width: 714px; height: 420px; overflow: hidden; }

  /* Front */
  .card-front {
    left: 238px; top: 117px;
    background: linear-gradient(180deg, var(--green-light) 0%, var(--green-mid) 55%, var(--green-dark) 100%);
  }
  .front-mark {
    position: absolute; left: 273px; top: 84px; width: 168px; height: 168px;
    border-radius: 50%; background: #129447;
  }
  .front-name {
    position: absolute; left: 0; right: 0; top: 292px; text-align: center;
    font-family: "Marcellus", serif; color: var(--white); line-height: 1;
  }
  .front-name .brand { display: block; font-size: 50px; letter-spacing: 1px; }
  .front-name .brand-sub { display: block; font-size: 14px; letter-spacing: 6px; margin-top: 2px; }

  /* Back */
  .card-back { left: 230px; top: 644px; background: var(--paper); }
  .back-waves { position: absolute; inset: 0; }
  .holder {
    position: absolute; right: 30px; top: 50px; text-align: right; color: var(--white);
  }
  .holder-name { font-family: "Saira Semi Condensed", sans-serif; font-weight: 600; font-size: 27px; line-height: 1; }
  .holder-title { font-family: "Lora", serif; font-size: 15px; margin-top: 8px; }

  .back-mark {
    position: absolute; left: 40px; top: 143px; width: 98px; height: 98px; border-radius: 50%;
    background: radial-gradient(circle at 40% 35%, #ffffff 0%, #e9e9e9 60%, #d3d3d3 100%);
  }
  .back-name {
    position: absolute; left: 170px; top: 160px; font-family: "Marcellus", serif;
    color: var(--green-brand); line-height: 1;
  }
  .back-name .brand { display: block; font-size: 43px; letter-spacing: 1px; }
  .back-name .brand-sub { display: block; font-size: 13px; letter-spacing: 6px; margin-top: 1px; padding-left: 68px; }

  .contacts {
    position: absolute; top: 290px; list-style: none; font-size: 17px; color: var(--ink);
  }
  .contacts li { display: flex; align-items: center; height: 26px; }
  .contacts svg { width: 17px; height: 17px; fill: var(--green-brand); margin-right: 13px; flex: none; }
  .contacts-phone { left: 38px; }
  .contacts-web { left: 252px; }
</style>
</head>
<body>

<section class="card card-front" aria-label="Card front">
  <div class="front-mark"></div>
  <h1 class="front-name">
    <span class="brand">VELDTMOOR</span>
    <span class="brand-sub">CAPITAL GROUP</span>
  </h1>
</section>

<section class="card card-back" aria-label="Card back">
  <svg class="back-waves" viewBox="0 0 714 420" preserveAspectRatio="none" aria-hidden="true">
    <defs>
      <linearGradient id="band" x1="0" y1="0" x2="1" y2="0">
        <stop offset="0" stop-color="#5bb94f"/>
        <stop offset="0.45" stop-color="#2e8f45"/>
        <stop offset="1" stop-color="#17683a"/>
      </linearGradient>
      <linearGradient id="swoosh" x1="0" y1="0" x2="1" y2="0">
        <stop offset="0" stop-color="#e4e4e4"/>
        <stop offset="0.5" stop-color="#8f8f8f"/>
        <stop offset="1" stop-color="#a8a8a8"/>
      </linearGradient>
    </defs>
    <path d="M0 0 H714 V166 C610 170 540 150 470 115 C370 60 250 20 130 22 C70 24 30 32 0 42 Z" fill="url(#band)"/>
    <path d="M0 50 C50 35 120 28 190 32 C300 40 380 80 460 130 C540 175 620 190 714 188 V180 C620 182 545 168 470 124 C380 70 290 28 190 26 C110 25 50 34 0 44 Z" fill="url(#swoosh)"/>
    <path d="M0 72 C70 45 160 36 240 44 C170 42 90 52 0 82 Z" fill="#d2d2d2"/>
    <path d="M90 68 C200 34 330 46 430 90 C330 54 210 48 90 68 Z" fill="#b8b8b8"/>
  </svg>

  <div class="holder">
    <p class="holder-name">Desmond Whitlake</p>
    <p class="holder-title">Managing Partner</p>
  </div>

  <div class="back-mark"></div>
  <h2 class="back-name">
    <span class="brand">VELDTMOOR</span>
    <span class="brand-sub">CAPITAL GROUP</span>
  </h2>

  <ul class="contacts contacts-phone">
    <li><svg viewBox="0 0 24 24" aria-label="Office"><path d="M3 8c0-2 2-4 9-4s9 2 9 4v2h-5V8H8v2H3z"/><path d="M6 12h12l2 9H4z"/></svg>415.555.0142</li>
    <li><svg viewBox="0 0 24 24" aria-label="Fax"><path d="M7 3h10v5H7z"/><path d="M3 9h18v9h-3v-4H6v4H3z"/><path d="M7 15h10v6H7z"/></svg>415.555.0147</li>
    <li><svg viewBox="0 0 24 24" aria-label="Mobile"><path d="M7 2h10a1 1 0 0 1 1 1v18a1 1 0 0 1-1 1H7a1 1 0 0 1-1-1V3a1 1 0 0 1 1-1zm1 3v13h8V5zm4 14.5a1 1 0 1 0 0 .1z"/></svg>415.555.0193</li>
  </ul>

  <ul class="contacts contacts-web">
    <li><svg viewBox="0 0 24 24" aria-label="Email"><path d="M2 5h20v14H2zm2 2v.5l8 6 8-6V7l-8 6z"/></svg>desmond@veldtmoorcapital.ventures</li>
    <li><svg viewBox="0 0 24 24" aria-label="Website"><path d="M12 2a10 10 0 1 0 0 20 10 10 0 0 0 0-20zm0 2c1 1.2 1.8 3 2.1 5H9.9C10.2 7 11 5.2 12 4zM4.3 11h3.6v2H4.3zm5.6 0h4.2v2H9.9zm6.2 0h3.6v2h-3.6zM9.9 15h4.2c-.3 2-1.1 3.8-2.1 5-1-1.2-1.8-3-2.1-5z"/></svg>www.veldtmoorcapital.ventures</li>
    <li><svg viewBox="0 0 24 24" aria-label="Address"><path d="M12 1a7 7 0 0 0-7 7c0 5.2 7 15 7 15s7-9.8 7-15a7 7 0 0 0-7-7zm0 4a3 3 0 1 1 0 6 3 3 0 0 1 0-6z"/></svg>187 Fenworth St San Francisco, CA 94187</li>
  </ul>
</section>

</body>
</html>
```